Business card for Crestline Bathrooms

Please design a business card for our bathroom renovation business. You can use my existing logo, but if you have an idea to modernize it, I would like to see it. Please see attached files first. I would like to use the blue and the orange theme. I like the concept of using the shower head in the logo. Please find following a design (or two) that I have been trying to create with my limited resources. That design was for a sign, but I was going to adopt it and use it as a business card as well. I like the concept of the water splash but I don’t think it “flows” nicely together with the logo. Another thought is that maybe creating the logo out of water splash could work and have a dramatic effect (like the water text and the butterfly picture attached with similar background instead of white). If the above doesn’t work I would like to see a modern simplified design. One of the attached files named as the unwanted business card has all the details that I want included in the business card. Please note that it is two sided.
Updates

I am very thankful for the designs that I have received, but they are very similar and only a couple of attempts to do something with the water splash as per my original brief. Modernizing the logo and having it made out of out of water splash with the orange as color accent could work and have a dramatic effect (like the water text and the butterfly picture attached with similar background instead of white). Please do not use the butterfly itself! This is just an example that images can be created out of water splash.

Contact Information for Business Card

all the details are on the unwonted business card file included

Colors
3176b5

Requirements
Nice to have
• Copied from the brief:
• ... maybe creating the logo out of water splash could work and have a dramatic effect (like the water text and the butterfly picture attached with similar background instead of white). Please do not use the butterfly itself!
Should not have
• I am getting designs with a butterfly. The butterfly picture was an example of creating something from a water splash. The butterfly itself has no association with anything other than the concept of creating a logo out of water splash. Sorry, I thought I was clear in the brief.

```html
<!DOCTYPE html>
<html lang="en">
<head>
<meta charset="utf-8">
<title>Crestline Bathrooms – Business Card</title>
<link rel="stylesheet" href="https://fonts.googleapis.com/css2?family=Roboto:wght@400;500;700&family=Roboto+Condensed:wght@700&display=swap">
<style>
  :root {
    --backdrop: #2f2f31;
    --card-white: #f2f2f2;
    --navy: #003f6b;
    --coral: #e9786b;
    --white: #ffffff;
  }
  * { margin: 0; padding: 0; box-sizing: border-box; }
  html, body { width: 1200px; height: 960px; overflow: hidden; }
  body {
    background: var(--backdrop);
    font-family: "Roboto", Arial, sans-serif;
    position: relative;
  }
  .card {
    position: absolute;
    width: 598px;
    height: 342px;
    border-radius: 20px;
    overflow: hidden;
  }
  .card--front { left: 322px; top: 108px; background: var(--card-white); }
  .card--back { left: 320px; top: 493px; background: var(--coral); }

  .wave { position: absolute; inset: 0; width: 100%; height: 100%; }

  .brand { position: absolute; font-weight: 500; line-height: 1; }
  .card--front .brand { right: 40px; top: 58px; color: var(--navy); text-align: right; }
  .brand__name { font-size: 40px; display: block; letter-spacing: 0.5px; }
  .brand__sub { font-size: 21px; display: block; letter-spacing: 3px; margin-top: 6px; }
  .brand__dot {
    position: absolute; width: 22px; height: 22px; border-radius: 50%;
    background: var(--coral); top: -26px; right: 0;
  }

  .holder {
    position: absolute; left: 26px; top: 207px;
    font-family: "Roboto Condensed", "Arial Narrow", sans-serif;
    font-weight: 700; font-size: 20px; color: var(--white); letter-spacing: 0.3px;
  }
  .contact-list {
    position: absolute; left: 27px; top: 249px;
    list-style: none; color: var(--white); font-size: 14.5px;
  }
  .contact-list li { display: flex; align-items: center; height: 19px; }
  .contact-list svg { width: 13px; height: 13px; margin-right: 9px; fill: var(--white); flex: none; }
  .postal {
    position: absolute; right: 24px; top: 295px;
    color: var(--white); font-size: 14.5px; text-align: right; line-height: 19px;
  }

  .card--back .brand {
    left: 0; right: 0; top: 52px; color: var(--white); text-align: center;
  }
  .card--back .brand__name { font-size: 46px; }
  .card--back .brand__sub { font-size: 22px; }
  .card--back .brand__dot { background: var(--white); top: -8px; right: 150px; width: 20px; height: 20px; }
  .services {
    position: absolute; left: 0; right: 0; top: 188px;
    list-style: none; text-align: center; color: var(--white);
    font-size: 14.5px; line-height: 18px;
  }
  .memberships {
    position: absolute; left: 0; right: 0; top: 276px;
    display: flex; justify-content: center; align-items: center; gap: 18px;
  }
  .badge { background: var(--white); }
  .badge--round { width: 32px; height: 34px; border-radius: 6px; }
  .badge--wide { width: 116px; height: 24px; border-radius: 3px; }
  .memberships__rule { width: 1px; height: 34px; background: var(--white); }
</style>
</head>
<body>

<section class="card card--front" aria-label="Card front">
  <svg class="wave" viewBox="0 0 598 342" preserveAspectRatio="none" aria-hidden="true">
    <path d="M0,84 C170,52 320,170 450,236 C530,274 586,248 598,186 L598,342 L0,342 Z" fill="var(--coral)"/>
    <path d="M0,100 C180,66 320,188 440,248 C520,282 582,262 598,204 L598,342 L0,342 Z" fill="var(--white)"/>
    <path d="M0,104 C180,70 320,192 440,252 C520,286 584,266 598,208 L598,342 L0,342 Z" fill="var(--navy)"/>
  </svg>

  <div class="brand">
    <span class="brand__dot"></span>
    <span class="brand__name">Crestline</span>
    <span class="brand__sub">Bathrooms</span>
  </div>

  <h1 class="holder">DANIEL WHITFORD</h1>
  <ul class="contact-list">
    <li><svg viewBox="0 0 24 24"><path d="M6.6 10.8a15.1 15.1 0 0 0 6.6 6.6l2.2-2.2c.3-.3.7-.4 1-.2 1.1.4 2.3.6 3.6.6.6 0 1 .4 1 1V20c0 .6-.4 1-1 1A17 17 0 0 1 3 4c0-.6.4-1 1-1h3.5c.6 0 1 .4 1 1 0 1.3.2 2.5.6 3.6.1.3 0 .7-.2 1z"/></svg>0400 555 218</li>
    <li><svg viewBox="0 0 24 24"><path d="M7 1h10a2 2 0 0 1 2 2v18a2 2 0 0 1-2 2H7a2 2 0 0 1-2-2V3a2 2 0 0 1 2-2zm0 3v14h10V4z"/></svg>6255 0147</li>
    <li><svg viewBox="0 0 24 24"><path d="M2 5h20v14H2zm2 2v.5l8 5 8-5V7l-8 5z"/></svg>daniel@crestlinebathrooms.com.au</li>
    <li><svg viewBox="0 0 24 24"><path d="M12 2a10 10 0 1 0 0 20 10 10 0 0 0 0-20zm-1 17.9A8 8 0 0 1 4 12l1-1 4 4v1a2 2 0 0 0 2 2zm6.9-2.5A2 2 0 0 0 16 16h-1v-3a1 1 0 0 0-1-1H8v-2h2a1 1 0 0 0 1-1V7h2a2 2 0 0 0 2-2v-.4a8 8 0 0 1 2.9 12.8z"/></svg>crestlinebathrooms.com.au</li>
  </ul>
  <address class="postal" style="font-style:normal">PO Box 41<br>Marlowe Vale 2700</address>
</section>

<section class="card card--back" aria-label="Card back">
  <div class="brand">
    <span class="brand__name">Crestline</span>
    <span class="brand__sub">Bathrooms</span>
  </div>
  <ul class="services">
    <li>Complete Bathroom Renovations &amp; Remodelling</li>
    <li>Highly Skilled &amp; Qualified Tradespeople</li>
    <li>Professional Service From Concept To Completion</li>
    <li>All Work Guaranteed</li>
  </ul>
  <div class="memberships" aria-label="Industry memberships">
    <span class="badge badge--round"></span>
    <span class="memberships__rule"></span>
    <span class="badge badge--wide"></span>
  </div>
</section>

</body>
</html>
```